Pawn & Gun store business card design

Hello! We would like a new business card design for our pawn & gun store. We loan money on items of value and sell firearms, jewelry, electronics & more.

Card will need to have the following information:

Business name - Prairie Nickel Pawn & Gun
Address - 2417 Hwy 53 S. Suite C Wylie, TX 75246
Employees name - Darren Kellum
Phone number - 972-613-8840
Email - PrairieNickelPawn@Mailvera.com
Website - PrairieNickelPawn.com

Somewhere on the card we would like it to say "Offering 10 Month Layaway!" & "We buy & loan on anything of value!". Our main store color is orange (please see logo). Logo does not have to be on the business card but it can be. Would like the back to have an area to write a note on the back. We like vintage things like old coins, collectables, firearms and more so think about this in the design. We want a business card as unique as our store!

Colors

Designer to choose colors to be used in the design.

Requirements
Nice to have
• Vintage Style

```html
<!DOCTYPE html>
<html lang="en">
<head>
<meta charset="utf-8">
<title>Prairie Nickel Pawn &amp; Gun — Business Card</title>
<link rel="stylesheet" href="https://fonts.googleapis.com/css2?family=Oswald:wght@300;400;700&display=swap">
<style>
  :root {
    --backdrop: #a9abad;
    --kraft: #cfae84;
    --ink: #3a2416;
    --ink-soft: rgba(58, 36, 22, 0.35);
    --orange: #d9601f;
    --edge: #c8581d;
  }
  * { margin: 0; padding: 0; box-sizing: border-box; }
  html, body { width: 1200px; height: 800px; overflow: hidden; }
  body {
    background: var(--backdrop);
    font-family: "Oswald", sans-serif;
    color: var(--ink);
    position: relative;
  }
  .card {
    position: absolute;
    top: 246px;
    width: 540px;
    height: 309px;
    background: var(--kraft);
    box-shadow: 0 0 0 2px var(--edge);
    padding: 12px;
  }
  .card--front { left: 40px; }
  .card--back { left: 620px; }
  .frame {
    width: 100%;
    height: 100%;
    border: 2px solid var(--ink);
  }
  .front-grid {
    display: grid;
    grid-template-columns: 95px 95px 1fr;
    grid-template-rows: 104px 1fr 1fr;
  }
  .front-grid > div {
    border-right: 2px solid var(--ink);
    border-bottom: 2px solid var(--ink);
    display: flex;
    align-items: center;
    overflow: hidden;
  }
  .name-row {
    grid-column: 1 / 4;
    justify-content: center;
    border-right: none !important;
  }
  .holder-name {
    font-weight: 700;
    font-size: 64px;
    line-height: 1;
    text-transform: uppercase;
    letter-spacing: 1px;
    white-space: nowrap;
  }
  .icon-cell { justify-content: center; }
  .icon-placeholder {
    width: 46px;
    height: 32px;
    background: #8a6a4c;
    border-radius: 3px;
  }
  .contact-cell, .offer-cell {
    border-right: none !important;
    flex-direction: column;
    align-items: flex-start !important;
    justify-content: center;
    padding-left: 14px;
    text-transform: uppercase;
    white-space: nowrap;
  }
  .contact-cell { font-weight: 400; font-size: 14px; line-height: 1.35; letter-spacing: 0.3px; }
  .address { font-weight: 300; }
  .phone-cell {
    grid-column: 1 / 3;
    justify-content: center;
    border-bottom: none !important;
  }
  .phone { font-weight: 700; font-size: 29px; white-space: nowrap; }
  .offer-cell { border-bottom: none !important; }
  .offer-title { font-weight: 700; font-size: 17px; letter-spacing: 0.3px; }
  .offer-sub { font-weight: 300; font-size: 14px; letter-spacing: 0.3px; }
  .back-frame {
    display: flex;
    flex-direction: column;
    align-items: center;
    justify-content: center;
    padding: 0 40px;
    gap: 34px;
  }
  .brand {
    display: flex;
    align-items: center;
    gap: 10px;
  }
  .brand-dot {
    width: 22px;
    height: 22px;
    border-radius: 50%;
    background: var(--orange);
  }
  .brand-name {
    font-weight: 700;
    font-size: 30px;
    color: var(--orange);
    text-transform: uppercase;
    letter-spacing: 1px;
    white-space: nowrap;
  }
  .note-area {
    width: 100%;
    display: flex;
    flex-direction: column;
    gap: 26px;
  }
  .note-line {
    height: 0;
    border-bottom: 1px solid var(--ink-soft);
  }
</style>
</head>
<body>
  <section class="card card--front">
    <div class="frame front-grid">
      <div class="name-row"><h1 class="holder-name">Darren Kellum</h1></div>
      <div class="icon-cell"><div class="icon-placeholder" role="img" aria-label="Vintage revolver illustration"></div></div>
      <div class="icon-cell"><div class="icon-placeholder" role="img" aria-label="Diamond illustration"></div></div>
      <div class="contact-cell">
        <span class="email">PrairieNickelPawn@Mailvera.com</span>
        <span class="website">www.PrairieNickelPawn.com</span>
        <span class="address">2417 Hwy 53 S. Suite C Wylie, TX 75246</span>
      </div>
      <div class="phone-cell"><span class="phone">972-613-8840</span></div>
      <div class="offer-cell">
        <span class="offer-title">Offering 10 Month Layaway</span>
        <span class="offer-sub">We buy &amp; loan on anything of value</span>
      </div>
    </div>
  </section>

  <section class="card card--back">
    <div class="frame back-frame">
      <div class="brand">
        <span class="brand-dot"></span>
        <span class="brand-name">Prairie Nickel Pawn</span>
      </div>
      <div class="note-area" aria-label="Space for a handwritten note">
        <div class="note-line"></div>
        <div class="note-line"></div>
        <div class="note-line"></div>
      </div>
    </div>
  </section>
</body>
</html>
```